KTR Photography Editing & Support Services for Real Estate

We require a double sided A4 flyer to promote our photography services to real estate agencies.
This particular service is targeted to rural areas where reliable, professional and highly skilled photographers are difficult to source. We teach the agent how to photograph, they upload files to a server and we take care of the rest (image editing, quality control and delivery). This will give the agents flexibility with when to shoot and eliminates the stress of managing a photographer / contractor. We offer a 1 day face to face training session and competitive packages for equipment start up.
We would like the flyer to look clean & very professional. The flyer should showcase samples of our work to highlight what can be achieved by using our services. We like the look of a black or dark background behind the text and feel that would look nice with our photographs provided. Otherwise open to your suggestions and ideas.
TEXT FOR FLYER:
Welcome to the KTR Real Estate Photography Editing and Support Service
• Take your real estate business to the next level by providing impressive real estate imagery that makes you stands out from the competition
• Omit the stress of trying to find a good photographer or managing an unreliable one and hence have more time to focus on other aspects of your business
• Showcase your listings with better quality and more impactful photographs than your competitors thereby increasing potential for a quick sale
• Great first impressions matter and you will achieve this by looking and feeling more professional. This will attract and retain more future clients.
HOW IT WORKS
• We understand that your time is valuable, so let us handle the editing and delivery of your images. You shoot, and we take care of the rest.
• Images are edited and delivered within 1 working day
INCLUSIONS:
• Full day face to face training (we come to you) and instructional handbook
• We will teach you everything you need to know about your equipment and how to take stunning real estate photographs
• Service turnaround within 1 working day
• Free HELP desk service Mon-Fri
• 12 month Exclusivity (rural towns only) for a limited time
INVESTMENT
• 99 per listing for us to manage images including editing, quality control and delivery (10 Images)
• Ask us about competitive packages for photography equipment if required
SUMMARY
The KTR Real Estate Photography Editing and Support Service is the perfect solution for busy real estate professionals who want to take their business to the next level. Our service is affordable, flexible, and designed to help you showcase your listings in the best possible light.
Contact us today to learn more about how we can help you.

```html
<!DOCTYPE html>
<html lang="en">
<head>
<meta charset="utf-8">
<title>KTR Real Estate Photography Flyer</title>
<link href="https://fonts.googleapis.com/css2?family=Montserrat:wght@300;400;500;600;700;800&display=swap" rel="stylesheet">
<style>
:root{
  --ink:#0c0c0d;
  --panel:#141415;
  --paper:#ffffff;
  --text:#f1f1f1;
  --muted:#bdbdbd;
  --rule:#6a6a6a;
  --stage:#d4d4d4;
}
*{box-sizing:border-box;margin:0;padding:0}
html,body{width:800px;height:1200px;overflow:hidden}
body{background:var(--stage);font-family:"Montserrat",sans-serif;color:var(--text);position:relative}
.spread{position:absolute;left:11px;top:329px;width:1324px;height:922px;transform:scale(0.5876);transform-origin:0 0;display:flex;gap:20px}
.page{position:relative;width:652px;height:922px;background:linear-gradient(135deg,#1b1b1c 0%,var(--ink) 45%,#161617 100%);overflow:hidden;box-shadow:0 6px 18px rgba(0,0,0,.25)}
.hero{position:absolute;left:0;top:0;width:652px;height:295px;background:radial-gradient(ellipse at 50% 45%,#2a2623 0%,#15130f 55%,#0a0a0a 100%)}
.hero-rule{position:absolute;left:0;top:295px;width:652px;height:2px;background:#d9d9d9}
.brand{position:absolute;left:0;width:652px;text-align:center;top:74px;font-weight:300;font-size:25px;letter-spacing:7px;color:#d8d8d8}
.brand-rule{position:absolute;left:288px;top:156px;width:76px;height:1px;background:#888}
.welcome{position:absolute;left:0;width:652px;top:200px;text-align:center;font-size:20px;font-weight:500;line-height:31px;color:#fff}
.welcome b{font-weight:800;font-size:25px}
.corner{position:absolute;width:34px;height:34px;border-color:#cfcfcf;border-style:solid}
.corner.tl{left:62px;top:184px;border-width:2px 0 0 2px}
.corner.br{left:556px;top:236px;border-width:0 2px 2px 0}
.label{position:absolute;left:243px;width:166px;height:31px;border:2px solid #e6e6e6;text-align:center;line-height:27px;font-weight:700;font-size:15px;letter-spacing:1px;color:#fff}
.cols{position:absolute;left:24px;width:604px;display:flex}
.col{flex:1;padding-right:10px}
.col+.col{border-left:1px solid var(--rule);padding-left:22px}
.item{display:flex;gap:8px;font-size:11.4px;line-height:13px;letter-spacing:.2px;margin-bottom:10px;color:#eaeaea}
.item svg{flex:0 0 18px;width:18px;height:18px;margin-top:-1px}
.hr{position:absolute;left:24px;width:604px;height:1px;background:var(--rule)}
.photo{position:absolute;width:194px;height:142px;border:1px solid #555}
.summary{position:absolute;left:24px;width:604px;top:742px;text-align:center;font-size:11px;line-height:13px;color:#eee}
.summary b{font-weight:700}
.footer{position:absolute;left:0;top:818px;width:652px;height:104px;background:var(--paper);display:flex;align-items:center;color:var(--ink)}
.cta{position:absolute;top:803px;left:245px;width:162px;height:31px;background:var(--ink);border:2px solid #fff;color:#fff;text-align:center;line-height:27px;font-size:14px;font-weight:700;z-index:2}
.contact{flex:1;text-align:center;font-size:12.5px;font-weight:700;padding-top:24px}
.contact.email{font-weight:400;flex:1.5;border-left:1px solid #999;border-right:1px solid #999}
.contact.email b{font-weight:700}
.contact svg{display:block;margin:0 auto 12px;width:24px;height:24px}
</style>
</head>
<body>
<svg width="0" height="0" style="position:absolute" aria-hidden="true">
  <symbol id="tick" viewBox="0 0 18 18"><circle cx="9" cy="9" r="7.8" fill="none" stroke="#fff" stroke-width="1.6"/><path d="M5.4 9.2l2.5 2.4 4.8-5" fill="none" stroke="#fff" stroke-width="1.8" stroke-linecap="round" stroke-linejoin="round"/></symbol>
  <symbol id="user" viewBox="0 0 24 24"><circle cx="12" cy="12" r="12" fill="#111"/><circle cx="12" cy="9.5" r="3" fill="none" stroke="#fff" stroke-width="1.4"/><path d="M7 17.5c.8-2.6 2.7-3.8 5-3.8s4.2 1.2 5 3.8z" fill="none" stroke="#fff" stroke-width="1.4"/></symbol>
  <symbol id="mail" viewBox="0 0 24 24"><circle cx="12" cy="12" r="12" fill="#111"/><rect x="6.5" y="8" width="11" height="8" fill="none" stroke="#fff" stroke-width="1.3"/><path d="M6.5 8l5.5 4.5L17.5 8" fill="none" stroke="#fff" stroke-width="1.3"/></symbol>
  <symbol id="phone" viewBox="0 0 24 24"><circle cx="12" cy="12" r="12" fill="#111"/><path d="M8.6 6.8l1.8-.3 1 2.6-1.3 1c.6 1.4 1.6 2.4 3 3l1-1.3 2.6 1-.3 1.8c-4.4.6-8.4-3.4-7.8-7.8z" fill="none" stroke="#fff" stroke-width="1.3" stroke-linejoin="round"/></symbol>
</svg>

<div class="spread">
  <!-- Front -->
  <section class="page page-front">
    <div class="hero" role="img" aria-label="Dimmed photograph of a modern dining room interior"></div>
    <div class="hero-rule"></div>
    <div class="brand">NORA ASHBY</div>
    <div class="brand-rule"></div>
    <span class="corner tl"></span><span class="corner br"></span>
    <h1 class="welcome"><b>Welcome</b> to the KTR Real Estate<br>Photography Editing and Support <b>Services</b></h1>

    <div class="label" style="top:320px">OUR SERVICES</div>
    <div class="cols" style="top:370px">
      <div class="col">
        <p class="item"><svg><use href="#tick"/></svg><span>Take your real estate business to the next level by providing impressive real estate imagery that makes you stands out from the competition</span></p>
        <p class="item"><svg><use href="#tick"/></svg><span>Omit the stress of trying to find a good photographer or managing an unreliable one and hence have more time to focus on other aspects of your business</span></p>
      </div>
      <div class="col">
        <p class="item"><svg><use href="#tick"/></svg><span>Showcase your listings with better quality and more impactful photographs than your competitors thereby increasing potential for a quick sale</span></p>
        <p class="item"><svg><use href="#tick"/></svg><span>Great first impressions matter and you will achieve this by looking and feeling more professional. This will attract and retain more future clients</span></p>
      </div>
    </div>
    <div class="hr" style="top:497px"></div>

    <div class="label" style="top:515px">HOW IT WORKS</div>
    <div class="cols" style="top:566px">
      <div class="col">
        <p class="item"><svg><use href="#tick"/></svg><span>We understand that your time is valuable, so let us handle the editing and delivery of your images. You shoot, and we take care of the rest.</span></p>
      </div>
      <div class="col">
        <p class="item"><svg><use href="#tick"/></svg><span>Images are edited and delivered within 1 working day</span></p>
      </div>
    </div>

    <div class="photo" style="left:24px;top:637px;background:linear-gradient(180deg,#7e8fa6 0%,#3a3430 55%,#4f5d3a 100%)" role="img" aria-label="Dark-clad farmhouse at dusk with lit windows"></div>
    <div class="photo" style="left:229px;top:637px;background:linear-gradient(180deg,#8ea0b8 0%,#d9b3a2 45%,#3d5a6e 62%,#4f7a3a 100%)" role="img" aria-label="Black timber cabin on a coastal clifftop at sunset"></div>
    <div class="photo" style="left:434px;top:637px;background:linear-gradient(180deg,#7b86b8 0%,#c9c4c8 45%,#e6e1da 75%,#a9a9a9 100%)" role="img" aria-label="White gabled house with warm lit interior at twilight"></div>

    <div class="cta">Contact Us Today</div>
    <footer class="footer">
      <div class="contact"><svg><use href="#user"/></svg>Nora Ashby</div>
      <div class="contact email"><svg><use href="#mail"/></svg>shoot@<b>noraashby</b>.com.au</div>
      <div class="contact"><svg><use href="#phone"/></svg>+61 400 555 017</div>
    </footer>
  </section>

  <!-- Back -->
  <section class="page page-back">
    <div class="brand">NORA ASHBY</div>
    <div class="brand-rule" style="opacity:0"></div>

    <div class="label" style="top:158px">INCLUSIONS</div>
    <div class="cols" style="top:206px">
      <div class="col" style="flex:1.1">
        <p class="item"><svg><use href="#tick"/></svg><span>Full day face to face training (we come to you) and instructional handbook</span></p>
        <p class="item"><svg><use href="#tick"/></svg><span>We will teach you everything you need to know about your equipment and how to take stunning real estate photographs</span></p>
      </div>
      <div class="col">
        <p class="item"><svg><use href="#tick"/></svg><span>Service turnaround within 1 working day</span></p>
        <p class="item"><svg><use href="#tick"/></svg><span>Free HELP desk service (Monday-Friday)</span></p>
        <p class="item"><svg><use href="#tick"/></svg><span>12 month Exclusivity (rural towns only) for a limited time</span></p>
      </div>
    </div>
    <div class="hr" style="top:298px"></div>

    <div class="label" style="top:316px">INVESTMENT</div>
    <div class="cols" style="top:368px">
      <div class="col" style="flex:1.1">
        <p class="item"><svg><use href="#tick"/></svg><span>99 per listing for us to manage images including editing, quality control and delivery (10 Images)</span></p>
      </div>
      <div class="col">
        <p class="item"><svg><use href="#tick"/></svg><span>Ask us about competitive packages for photography equipment if required</span></p>
      </div>
    </div>

    <div class="photo" style="left:24px;top:425px;background:linear-gradient(160deg,#e4ddd4 0%,#cfc4b6 60%,#b99a78 100%)" role="img" aria-label="Bright bathroom with freestanding bath and timber vanity"></div>
    <div class="photo" style="left:229px;top:425px;background:linear-gradient(180deg,#8a6a4a 0%,#2d4f7a 40%,#3a3230 75%,#7a6a5a 100%)" role="img" aria-label="Timber-ceilinged living room with large glass wall"></div>
    <div class="photo" style="left:434px;top:425px;background:linear-gradient(160deg,#f2f0ec 0%,#c8ccc4 55%,#e8e6e2 100%)" role="img" aria-label="Bright bedroom with white linen and garden views"></div>
    <div class="photo" style="left:24px;top:579px;background:linear-gradient(90deg,#6b5a48 0%,#cfc9c0 50%,#8a7a66 100%)" role="img" aria-label="Long hallway with timber bench and framed pictures"></div>
    <div class="photo" style="left:229px;top:579px;background:linear-gradient(180deg,#e9e6e1 0%,#d4cfc7 55%,#a47a52 100%)" role="img" aria-label="Open-plan kitchen and dining area with timber floors"></div>
    <div class="photo" style="left:434px;top:579px;background:linear-gradient(160deg,#4a4f58 0%,#2a2c31 55%,#9a9a9a 100%)" role="img" aria-label="Dark-walled lounge with charcoal sofa and side table"></div>

    <p class="summary"><b>The KTR Real Estate Photography Editing and Support Service</b> is the perfect solution for busy real estate professionals who want to take their business to the next level. Our service is affordable, flexible and designed to help you showcase your listings in the <b>best possible light</b>.</p>

    <div class="cta" style="left:233px;width:186px">CONTACT US TODAY</div>
    <footer class="footer">
      <div class="contact"><svg><use href="#user"/></svg>Nora Ashby</div>
      <div class="contact email"><svg><use href="#mail"/></svg>shoot@<b>noraashby</b>.com.au</div>
      <div class="contact"><svg><use href="#phone"/></svg>+61 400 555 017</div>
    </footer>
  </section>
</div>
</body>
</html>
```